Federal IT Consulting Company - Brisolux Consulting Group

We're seeking a skilled web designer to create a modern, bold, and engaging WordPress website for Brisolux Consulting Group, LLC. Our company specializes in federal IT consulting, and our name is a play on "Brightening Solutions." The website should reflect our expertise in the federal technology marketplace and position us as a trusted partner for clients navigating their IT journey.

contact: info@brisoluxgrp-example.com

Current Status

WordPress is already installed on our hosting account
We have an existing logo (may need modernization)

Design Requirements

Style:

Modern and visually striking design
Bold elements to convey confidence and expertise
Incorporate the concept of "brightening solutions" into the design

Features:

Modern UX sliders for dynamic content presentation
Eye-catching, high-quality images (stock photos to be sourced by the designer)
Responsive design for all devices

Color Scheme:

To be proposed by the designer, should align with our brand and convey trust and technological expertise

Logo:

Evaluate our current logo
Create a transparent background version if needed
Propose modernization if deemed necessary

Accessibility:

Ensure design elements are accessible to users with disabilities
Use high contrast ratios for text and background colors
Provide text alternatives for non-text content

Website Structure
Create the following pages, with the possibility of subpages:

Home
Services
About
Contact

Specific Page Requirements
Home Page

Striking hero section with a clear value proposition
Overview of our services
Client testimonials or trust indicators

Services Page

Detailed list of our IT consulting services
Clear explanation of how we help navigate the federal IT landscape

About Page

Company history and mission
Team highlights (if applicable)
Our approach to federal IT consulting

Contact Page

Contact form
Other contact methods (phone, email)

Technical Requirements

Fully responsive design
SEO best practices implemented
Fast loading times
Integration with necessary plugins (to be discussed)
Training on how to update and maintain the site
Full compliance with Web Content Accessibility Guidelines (WCAG) 2.1 Level AA
Adherence to Section 508 standards for federal website accessibility
Implementation of necessary features for ADA compliance
Updates

Designs look the same

Target Market(s)

US Federal Govt customers looking for IT support.

Industry/Entity Type

IT Consulting

Coding

Coded - Design and coding required

Colors
0054AA
0677BA
7BADD7
CADEEF
E8F1F8
0094D4
00A9DD
6FCCEA
C7EBF8
E9F6FB
00AB8E
00BBA5
67D7C9
C6EFE9
E9F9F6

```html
<!DOCTYPE html>
<html lang="en">
<head>
<meta charset="utf-8">
<title>Brisolux Consulting Group — Federal IT Consulting</title>
<link href="https://fonts.googleapis.com/css2?family=Michroma&family=Poppins:wght@400;500;600;700;800&display=swap" rel="stylesheet">
<style>
:root{
  --navy:#0a1f3d;
  --navy-2:#0f2a4f;
  --blue:#0677BA;
  --blue-bright:#0094D4;
  --cyan:#00A9DD;
  --sky:#7BADD7;
  --pale:#E8F1F8;
  --ice:#E9F6FB;
  --text:#1b2536;
  --muted:#5b6577;
  --white:#ffffff;
  --gold:#f5b400;
}
*{box-sizing:border-box;margin:0;padding:0}
html,body{width:1200px;height:3892px;overflow:hidden}
body{font-family:"Poppins",sans-serif;color:var(--text);background:var(--white);position:relative}
.abs{position:absolute}
.label{font-size:12px;font-weight:600;letter-spacing:1.5px;color:var(--navy);text-transform:uppercase;display:flex;align-items:center;gap:8px}
.label::before{content:"";width:3px;height:16px;background:var(--blue-bright)}
.title{font-weight:700;color:var(--navy);font-size:34px;line-height:1.2}
.title span{color:var(--blue-bright)}
.btn{display:inline-block;border-radius:30px;font-size:13px;font-weight:600;padding:12px 26px}
.btn-primary{background:var(--blue);color:var(--white)}
.btn-ghost{background:var(--white);color:var(--navy);border:1px solid #cfd8e3}
.para{font-size:13px;line-height:1.75;color:var(--muted)}
.photo{border-radius:14px}

/* header */
.site-header{top:0;left:0;width:1200px;height:90px;display:flex;align-items:center;justify-content:space-between;padding:0 140px;z-index:5}
.brand{display:flex;align-items:center;gap:10px;font-weight:800;font-size:26px;color:var(--navy);letter-spacing:.5px}
.brand-dot{width:30px;height:30px;border-radius:50%;background:var(--blue-bright)}
.nav{display:flex;align-items:center;gap:46px;font-size:14px;font-weight:500}
.nav a{color:var(--navy);text-decoration:none}
.nav a.active{color:var(--blue)}

/* hero */
.hero{top:0;left:0;width:1200px;height:600px;background:linear-gradient(90deg,#f4f8fc 0%,#eef3f9 32%,#c9d8e8 55%,#9fb6cf 75%,#7f9a7c 100%)}
.hero-photo{right:0;top:0;width:760px;height:600px;background:linear-gradient(180deg,#cfe0f0 0%,#e6eef6 40%,#b9c4cf 75%,#6f8a63 100%);-webkit-mask:linear-gradient(90deg,transparent,#000 35%);mask:linear-gradient(90deg,transparent,#000 35%)}
.hero-copy{left:140px;top:160px;width:560px}
.hero h1{font-family:"Michroma",sans-serif;font-size:40px;line-height:1.2;color:var(--navy);text-transform:uppercase}
.hero h2{margin-top:18px;font-family:"Michroma",sans-serif;font-size:17px;line-height:1.45;color:var(--navy);text-transform:uppercase}
.hero-actions{margin-top:46px;display:flex;gap:16px}

/* about */
.about-deco{left:142px;top:642px;width:80px;height:80px;border-radius:50%;background:var(--pale)}
.about-photo{left:180px;top:690px;width:300px;height:300px;background:linear-gradient(135deg,#9fb8cf,#4e6f93 60%,#2c3f5a)}
.about-photo-2{left:400px;top:880px;width:150px;height:150px;border:5px solid var(--white);background:linear-gradient(135deg,#6e8fb5,#1f3a62)}
.about-copy{left:630px;top:700px;width:430px}
.about-copy .title{margin:10px 0 22px}
.about-copy .para+.para{margin-top:14px}

/* services */
.band{left:0;top:1380px;width:1200px;height:760px;background:var(--navy)}
.band-ring{border:24px solid rgba(255,255,255,.05);border-radius:50%}
.services-head{left:140px;top:1130px;width:920px;display:flex;justify-content:space-between;align-items:flex-end}
.services-head .title{margin-top:10px}
.btn-small{padding:10px 22px;border-radius:8px;background:var(--blue);color:var(--white);font-size:13px;font-weight:600}
.service-card{top:1268px;width:292px;height:252px;border-radius:14px;overflow:hidden}
.service-card .label-bar{position:absolute;left:14px;right:14px;bottom:16px;display:flex;justify-content:space-between;align-items:center;color:var(--white);font-size:14px;font-weight:600}
.arrow-circle{width:30px;height:30px;border-radius:50%;background:var(--white);display:flex;align-items:center;justify-content:center}
.card-cyber{left:140px;background:linear-gradient(160deg,#3b2a7a,#1d1650 60%,#0e0b30)}
.card-cyber .label-bar{display:block;bottom:20px}
.card-cyber small{display:block;font-size:11px;font-weight:400;line-height:1.5;margin-top:6px;width:160px;opacity:.9}
.card-cloud{left:452px;background:linear-gradient(160deg,#2a5d9a,#183764 60%,#0c1d3c)}
.card-strategy{left:768px;background:linear-gradient(160deg,#c7d3df,#8aa0b8 55%,#3d5777)}
.slider-arrows{left:0;top:1562px;width:1200px;display:flex;justify-content:center;gap:16px}
.slider-arrows span{width:36px;height:36px;border-radius:50%;display:flex;align-items:center;justify-content:center;border:1px solid rgba(255,255,255,.5)}
.slider-arrows span.on{background:var(--blue-bright);border-color:var(--blue-bright)}

/* testimonials */
.testi-photo{left:140px;top:1680px;width:440px;height:380px;border-radius:0 14px 14px 0;background:linear-gradient(135deg,#dfe6ee,#9fb2c6 50%,#4b6584)}
.play{left:330px;top:1838px;width:56px;height:56px;border-radius:50%;background:var(--blue-bright);display:flex;align-items:center;justify-content:center}
.clients-badge{left:460px;top:2008px;background:var(--white);border-radius:12px;padding:10px 14px;display:flex;align-items:center;gap:10px;font-size:12px;font-weight:600;color:var(--navy);box-shadow:0 6px 20px rgba(0,0,0,.15)}
.clients-badge i{display:inline-block;width:20px;height:20px;border-radius:50%;border:2px solid var(--white);margin-left:-8px}
.testi-copy{left:610px;top:1710px;width:450px;color:var(--white)}
.testi-copy .label{color:var(--white)}
.testi-copy .title{color:var(--white);margin:10px 0 18px;font-size:30px;white-space:nowrap}
.stars{color:var(--gold);font-size:20px;letter-spacing:4px}
.testi-copy .para{color:#c5d1e0;margin-top:14px}
.author{position:relative;margin-top:34px;display:flex;align-items:center;gap:12px;border-top:1px solid rgba(255,255,255,.2);padding-top:20px}
.avatar{width:44px;height:44px;border-radius:50%;background:linear-gradient(135deg,#8aa1ba,#3a5273)}
.author b{display:block;font-size:14px}
.author small{font-size:11px;color:#b6c3d4}
.quote-mark{position:absolute;right:50px;top:-20px;width:40px;height:40px;border-radius:50%;background:var(--blue-bright);color:var(--white);font-weight:800;font-size:22px;display:flex;align-items:center;justify-content:center}

/* team */
.team-head{left:0;top:2200px;width:1200px;text-align:center}
.team-head .label{justify-content:center}
.team-head .title{margin-top:10px}
.member{top:2320px;width:200px;text-align:center}
.member .pic{width:184px;height:184px;margin:0 auto;border-radius:50%;border:4px solid var(--blue-bright);background:linear-gradient(180deg,#e3ebf3,#a9bccf)}
.member b{display:block;margin-top:16px;font-size:15px;color:var(--navy)}
.member small{display:block;font-size:11px;color:var(--blue-bright);margin-top:2px}
.member .socials{display:flex;justify-content:center;gap:8px;margin-top:10px}
.member .socials i{width:24px;height:24px;border-radius:50%;background:var(--navy);display:inline-block}

/* cta */
.cta{left:140px;top:2760px;width:920px;height:320px;border-radius:40px;background:linear-gradient(100deg,var(--blue),var(--blue-bright) 60%,var(--cyan))}
.cta-ring{border:22px solid rgba(255,255,255,.12);border-radius:50%}
.cta-copy{left:200px;top:2830px;width:420px;color:var(--white)}
.cta-copy h3{font-size:28px;line-height:1.3;font-weight:700}
.cta-copy p{font-size:13px;line-height:1.7;margin:14px 0 26px;color:#e3f1fb}
.cta-copy .btn{background:var(--white);color:var(--blue);border-radius:8px}
.cta-person{left:690px;top:2680px;width:290px;height:400px;border-radius:150px 150px 0 0;background:linear-gradient(180deg,#d8e2ec,#7d95b2 60%,#2c4a72)}

/* certificates */
.cert-head{left:0;top:3170px;width:1200px;text-align:center}
.cert-head .label{justify-content:center}
.cert-head .title{margin-top:10px}
.cert{top:3290px;width:250px;height:190px;border-radius:6px;box-shadow:0 6px 18px rgba(10,31,61,.12);background:var(--white);padding:18px}
.cert .frame{width:100%;height:100%;border:2px solid #d7c08a}
.cert .seal{position:absolute;width:34px;height:34px;border-radius:50%;background:#c9a449;right:34px;bottom:34px}
.cert.blue .frame{border-color:var(--navy)}
.cert-arrow{top:3366px;width:36px;height:36px;border-radius:50%;display:flex;align-items:center;justify-content:center}

/* footer */
.footer{left:0;top:3552px;width:1200px;height:340px;background:var(--navy);color:var(--white)}
.footer .brand{position:absolute;left:140px;top:60px;color:var(--white);font-size:30px}
.footer .tag{position:absolute;left:180px;top:100px;font-size:10px;letter-spacing:3px;color:#9fb2c8;text-transform:uppercase}
.fcol{position:absolute;top:60px;font-size:13px}
.fcol h4{font-size:14px;color:var(--blue-bright);font-weight:600;margin-bottom:14px}
.fcol li{list-style:none;color:#d3dbe6;margin-bottom:10px;display:flex;gap:8px;align-items:flex-start;line-height:1.5}
.fcol svg{flex:none;margin-top:3px}
.footer-bottom{position:absolute;left:140px;top:270px;width:920px;border-top:1px solid rgba(255,255,255,.15);padding-top:22px;display:flex;justify-content:space-between;align-items:center;font-size:12px;color:#b6c3d4}
.footer-bottom .socials{display:flex;gap:10px}
.footer-bottom .socials i{width:26px;height:26px;border-radius:50%;background:var(--blue-bright);display:inline-block}
</style>
</head>
<body>

<section class="hero abs">
  <div class="hero-photo abs" role="img" aria-label="Photo of the US Capitol dome under a bright sky with trees in front"></div>
  <div class="hero-copy abs">
    <h1>Navigate Your Federal IT Journey With Confidence</h1>
    <h2>Expert consulting services to guide your IT strategy</h2>
    <div class="hero-actions">
      <span class="btn btn-primary">Explore Our Services</span>
      <span class="btn btn-ghost">Get A Free Consultation</span>
    </div>
  </div>
</section>

<header class="site-header abs">
  <div class="brand"><span class="brand-dot"></span>Brisolux</div>
  <nav class="nav">
    <a class="active">Home</a><a>About Us</a><a>Services</a>
    <span class="btn btn-primary" style="padding:10px 22px">Contact Us</span>
  </nav>
</header>

<section class="about">
  <div class="about-deco abs"></div>
  <div class="about-photo photo abs" role="img" aria-label="Photo of a team meeting with a presenter at a screen"></div>
  <div class="about-photo-2 photo abs" role="img" aria-label="Photo of colleagues discussing work at a desk"></div>
  <div class="about-copy abs">
    <div class="label">About Us</div>
    <h2 class="title">Why Choose <span>Brisolux?</span></h2>
    <p class="para">There are many variations of passages of Lorem Ipsum available, but the majority have suffered alteration in some form, by injected humour, or randomised words which don't look even slightly believable. If you are going to use a passage of Lorem Ipsum, you need to be sure there isn't anything embarrassing hidden in the middle of text.</p>
    <p class="para">It is a long established fact that a reader will be distracted by the readable content of a page when looking at its layout.</p>
    <span class="btn btn-primary" style="margin-top:24px;border-radius:8px">Learn More</span>
  </div>
</section>

<div class="band abs"></div>
<div class="band-ring abs" style="left:-90px;top:1560px;width:240px;height:240px"></div>
<div class="band-ring abs" style="left:1010px;top:1400px;width:240px;height:240px"></div>

<section class="services">
  <div class="services-head abs">
    <div>
      <div class="label">Popular Services</div>
      <h2 class="title">The Best Solution For<br>Your <span>Business</span></h2>
    </div>
    <span class="btn-small">View All</span>
  </div>
  <article class="service-card card-cyber abs" role="img" aria-label="Photo of a digital security lock interface">
    <div class="label-bar">Cybersecurity<small>There are many variations of passages of Lorem Ipsum available.</small></div>
    <span class="arrow-circle abs" style="right:14px;bottom:20px"><svg width="12" height="12" viewBox="0 0 12 12"><path d="M2 6h8M7 3l3 3-3 3" stroke="#0a1f3d" stroke-width="1.6" fill="none"/></svg></span>
  </article>
  <article class="service-card card-cloud abs" role="img" aria-label="Photo of a hand touching a glowing cloud network">
    <div class="label-bar">Cloud Services<span class="arrow-circle"><svg width="12" height="12" viewBox="0 0 12 12"><path d="M2 6h8M7 3l3 3-3 3" stroke="#0a1f3d" stroke-width="1.6" fill="none"/></svg></span></div>
  </article>
  <article class="service-card card-strategy abs" role="img" aria-label="Photo of consultants planning strategy at a whiteboard">
    <div class="label-bar">IT Strategy Consulting<span class="arrow-circle"><svg width="12" height="12" viewBox="0 0 12 12"><path d="M2 6h8M7 3l3 3-3 3" stroke="#0a1f3d" stroke-width="1.6" fill="none"/></svg></span></div>
  </article>
  <div class="slider-arrows abs">
    <span><svg width="14" height="14" viewBox="0 0 14 14"><path d="M12 7H2M6 3 2 7l4 4" stroke="#fff" stroke-width="1.6" fill="none"/></svg></span>
    <span class="on"><svg width="14" height="14" viewBox="0 0 14 14"><path d="M2 7h10M8 3l4 4-4 4" stroke="#fff" stroke-width="1.6" fill="none"/></svg></span>
  </div>
</section>

<section class="testimonials">
  <div class="testi-photo abs" role="img" aria-label="Photo of professionals talking at a bright office table"></div>
  <div class="play abs"><svg width="18" height="18" viewBox="0 0 18 18"><path d="M5 3l10 6-10 6z" fill="#fff"/></svg></div>
  <div class="clients-badge abs">250+ Global<br>Clients
    <span style="margin-left:8px"><i style="background:#0094D4"></i><i style="background:#f5b400"></i><i style="background:#00AB8E"></i><i style="background:#e0457b"></i></span>
  </div>
  <div class="testi-copy abs">
    <div class="label">Our Testimonials</div>
    <h2 class="title">Hear What Our <span>Clients Say</span></h2>
    <div class="stars">★★★★★</div>
    <p class="para">It is a long established fact that a reader will be distracted by the readable content of a page when looking at its layout. The point of using Lorem Ipsum is that it has a more-or-less normal distribution of letters, as opposed to using 'Content here, content here', making it look like readable English.</p>
    <div class="author">
      <span class="avatar" role="img" aria-label="Client portrait"></span>
      <div><b>Calvin R. Ashmore</b><small>CEO &amp; Founder</small></div>
      <span class="quote-mark">”</span>
    </div>
  </div>
</section>

<section class="team">
  <div class="team-head abs">
    <div class="label">Our Team</div>
    <h2 class="title">Meet The Our <span>Experts</span></h2>
  </div>
  <div class="member abs" style="left:160px"><div class="pic" role="img" aria-label="Portrait of team member"></div><b>Owen Tarrell</b><small>Web Designer</small><div class="socials"><i></i><i></i></div></div>
  <div class="member abs" style="left:392px"><div class="pic" role="img" aria-label="Portrait of team member"></div><b>Felix Brandow</b><small>Web Designer</small><div class="socials"><i></i><i></i></div></div>
  <div class="member abs" style="left:628px"><div class="pic" role="img" aria-label="Portrait of team member"></div><b>Mara Ellwin</b><small>Web Designer</small><div class="socials"><i></i><i></i></div></div>
  <div class="member abs" style="left:860px"><div class="pic" role="img" aria-label="Portrait of team member"></div><b>Jonah Pierce</b><small>Web Designer</small><div class="socials"><i></i><i></i></div></div>
</section>

<section class="cta-wrap">
  <div class="cta abs"></div>
  <div class="cta-ring abs" style="left:560px;top:2980px;width:160px;height:160px;clip-path:inset(0 0 60px 0)"></div>
  <div class="cta-copy abs">
    <h3>We Are Federal IT Consulting<br>We Make Future!</h3>
    <p>There are many variations of passages of Lorem Ipsum available, but the majority have suffered alteration in some form.</p>
    <span class="btn">Get Started Now</span>
  </div>
  <div class="cta-person abs" role="img" aria-label="Photo of a smiling consultant holding a laptop"></div>
</section>

<section class="certificates">
  <div class="cert-head abs">
    <div class="label">Certifications</div>
    <h2 class="title">Certificates Of The Most<br>Popular <span>Brands</span></h2>
  </div>
  <div class="cert-arrow abs" style="left:140px;border:1px solid #c8d3e0"><svg width="14" height="14" viewBox="0 0 14 14"><path d="M9 3 5 7l4 4" stroke="#0a1f3d" stroke-width="1.6" fill="none"/></svg></div>
  <div class="cert abs" style="left:200px"><div class="frame"></div><span class="seal"></span></div>
  <div class="cert blue abs" style="left:475px"><div class="frame"></div><span class="seal" style="background:#0a1f3d"></span></div>
  <div class="cert abs" style="left:750px"><div class="frame" style="border-color:#9aa6b4"></div><span class="seal"></span></div>
  <div class="cert-arrow abs" style="left:1024px;background:var(--blue-bright)"><svg width="14" height="14" viewBox="0 0 14 14"><path d="M5 3l4 4-4 4" stroke="#fff" stroke-width="1.6" fill="none"/></svg></div>
</section>

<footer class="footer abs">
  <div class="brand"><span class="brand-dot"></span>Brisolux</div>
  <div class="tag">Brightening Solutions</div>
  <div class="fcol" style="left:500px"><h4>Quick Links</h4><ul><li>Home</li><li>About Us</li><li>Services</li></ul></div>
  <div class="fcol" style="left:670px"><h4>Resources</h4><ul><li>Privacy Policy</li><li>Terms Of Service</li></ul></div>
  <div class="fcol" style="left:850px;width:210px"><h4>Contact Info</h4><ul>
    <li><svg width="12" height="14" viewBox="0 0 12 14"><path d="M6 13S1 8 1 5a5 5 0 0 1 10 0c0 3-5 8-5 8z" fill="#0094D4"/><circle cx="6" cy="5" r="1.8" fill="#0a1f3d"/></svg>418 Harbor Point Avenue, Suite 210, Reston 2024</li>
    <li><svg width="14" height="12" viewBox="0 0 14 12"><rect x="1" y="1" width="12" height="10" rx="1.5" fill="none" stroke="#0094D4" stroke-width="1.4"/><path d="M1 2l6 5 6-5" stroke="#0094D4" stroke-width="1.4" fill="none"/></svg>info@brisoluxgrp-example.com</li>
    <li><svg width="13" height="13" viewBox="0 0 13 13"><path d="M3 1l2 3-1.3 1.3a7 7 0 0 0 4 4L9 8l3 2-1 2C6 12 1 7 1 2z" fill="#0094D4"/></svg>000-555-0147</li>
  </ul></div>
  <div class="footer-bottom"><span>© 2024 Brisolux. All rights reserved.</span><span class="socials"><i></i><i></i><i></i><i></i></span></div>
</footer>

</body>
</html>
```